Business card design

I am open to ideas. I was thinking of a vertical design, turning the name 90 degrees and placing it on the left edge, then some clipped portion of the fabulous tree with contact info on the bottom -- special emphasis on Web address:WhimBeads.comFor All Your Beading Needs121 E. Cotati AveCotati, CA 94931(707) 664-8343

```html
<!DOCTYPE html>
<html lang="en">
<head>
<meta charset="utf-8">
<title>Fern &amp; Glass — Business Card</title>
<link rel="stylesheet" href="https://fonts.googleapis.com/css2?family=Arvo:wght@400;700&display=swap">
<style>
  :root {
    --backdrop: #8c8c8c;
    --card-white: #ffffff;
    --card-black: #000000;
    --ink-light: #ffffff;
    --ink-dark: #111111;
    --accent-purple: #8e6bb5;
    --accent-green: #9ccc3c;
    --accent-red: #e2343b;
  }
  html, body {
    margin: 0;
    width: 1200px;
    height: 1200px;
    overflow: hidden;
    background: var(--backdrop);
  }
  .card {
    position: absolute;
    left: 300px;
    top: 110px;
    width: 600px;
    height: 980px;
    background: var(--card-white);
    font-family: "Arvo", serif;
    box-shadow: 3px 4px 8px rgba(0,0,0,0.35);
    overflow: hidden;
  }
  .card-diagonal {
    position: absolute;
    inset: 0;
  }
  .brand {
    position: absolute;
    left: 0;
    right: 0;
    top: 300px;
    display: flex;
    align-items: center;
    justify-content: center;
    gap: 16px;
  }
  .brand-dot {
    width: 22px;
    height: 22px;
    border-radius: 50%;
    background: var(--ink-dark);
  }
  .brand-name {
    font-size: 44px;
    font-weight: 400;
    color: var(--ink-dark);
  }
  .contact-line {
    position: absolute;
    right: 58px;
    margin: 0;
    color: var(--ink-light);
    text-align: right;
    white-space: nowrap;
  }
  .web { top: 555px; font-size: 32px; font-weight: 700; }
  .phone { top: 600px; font-size: 31px; }
  .street { top: 697px; font-size: 31px; right: 63px; }
  .city { top: 741px; font-size: 31px; right: 63px; }
  .tagline { top: 855px; font-size: 31px; right: 63px; }
  .divider {
    position: absolute;
    left: 375px;
    width: 157px;
    height: 2px;
    background: var(--ink-light);
  }
  .divider-one { top: 674px; }
  .divider-two { top: 831px; }
  .accent-bar {
    position: absolute;
    left: 563px;
    width: 5px;
  }
  .bar-purple { top: 565px; height: 76px; background: var(--accent-purple); }
  .bar-green { top: 709px; height: 76px; background: var(--accent-green); }
  .bar-red { top: 843px; height: 76px; background: var(--accent-red); }
</style>
</head>
<body>
  <div class="card">
    <svg class="card-diagonal" width="600" height="980" viewBox="0 0 600 980" aria-hidden="true">
      <polygon points="0,554 600,319 600,980 0,980" fill="var(--card-black)"/>
    </svg>

    <div class="brand">
      <span class="brand-dot"></span>
      <span class="brand-name">Fern &amp; Glass</span>
    </div>

    <p class="contact-line web">FernGlassco.com</p>
    <p class="contact-line phone">(707) 555-0192</p>
    <span class="accent-bar bar-purple"></span>

    <span class="divider divider-one"></span>

    <p class="contact-line street">348 W. Brindle Ave</p>
    <p class="contact-line city">Larkdale, CA 94990</p>
    <span class="accent-bar bar-green"></span>

    <span class="divider divider-two"></span>

    <p class="contact-line tagline">For All Your Beading Needs</p>
    <span class="accent-bar bar-red"></span>
  </div>
</body>
</html>
```